Looking for a5 flyer for domestic properties in Scotland
One side on Air Source Heat pumps (air to water Heat pump) Instalation + maintenance
Other side Air to Air Heat Pumps also knows as Air Conditioning Heat Pumps. Installation
Design to be Black white with red blue
Harlow- Climawell Services

Need sell the benifts of large energy savings over oil and lpg and lowering carbon footprint

```html
<!DOCTYPE html>
<html lang="en">
<head>
<meta charset="utf-8">
<title>Harlow- Climawell Services – Heat Pump Flyer, Both Sides</title>
<link rel="stylesheet" href="https://fonts.googleapis.com/css2?family=Rubik:wght@300;400;600;700&family=Arimo:wght@400;700&family=Roboto+Condensed:wght@700&display=swap">
<style>
  :root {
    --ink: #221f20;
    --white: #ffffff;
    --sky: #1ba6ea;
    --deep-blue: #0b56b3;
    --orange: #f6801f;
    --orange-deep: #ef6b1c;
    --rule-light: rgba(255,255,255,0.45);
    --rule-dark: #c9c9c9;
    --backdrop: #dcdee1;
  }
  * { box-sizing: border-box; margin: 0; padding: 0; }
  html, body { width: 868px; height: 1200px; overflow: hidden; background: var(--backdrop); }
  .canvas { position: relative; width: 868px; height: 1200px; overflow: hidden; }

  .sheet { position: absolute; top: 314px; width: 404px; height: 573px; overflow: hidden; box-shadow: 0 4px 12px rgba(0,0,0,0.18); }
  .sheet--front { left: 20px; }
  .sheet--back { left: 444px; }
  .flyer {
    position: absolute; left: 0; top: 0; width: 580px; height: 822px; overflow: hidden;
    transform: scale(0.69655); transform-origin: top left;
    background: var(--white); font-family: "Arimo", Arial, sans-serif; color: var(--ink);
  }
  .layer { position: absolute; left: 0; top: 0; }

  /* ---------- Front: air source heat pumps ---------- */
  .hero-band { position: absolute; left: 0; top: 0; width: 580px; height: 285px; background: var(--ink); }
  .family-photo {
    position: absolute; left: 300px; top: 0; width: 280px; height: 285px;
    background: linear-gradient(90deg, var(--ink) 0%, rgba(150,120,100,0.6) 30%, #c9b3a0 65%, #b99a84 100%);
  }
  .headline { position: absolute; left: 33px; top: 36px; font-family: "Rubik", sans-serif; font-weight: 600; }
  .headline span { display: block; color: var(--sky); font-size: 38px; line-height: 43px; letter-spacing: -0.8px; }
  .headline .light { font-weight: 300; font-size: 41px; }
  .headline .accent { color: var(--orange); font-size: 45px; font-weight: 700; line-height: 44px; }
  .subhead { position: absolute; left: 33px; top: 213px; color: var(--white); font-weight: 700; font-size: 16px; line-height: 20px; }

  .intro { position: absolute; left: 28px; top: 307px; width: 215px; padding-left: 14px; border-left: 4px solid var(--orange); height: 138px; }
  .intro h2 { font-size: 19px; line-height: 24px; font-weight: 700; }
  .intro p { margin-top: 4px; font-size: 10.3px; line-height: 13.3px; }

  .pump-photo {
    position: absolute; left: 330px; top: 285px; width: 250px; height: 345px;
    background: linear-gradient(180deg, #eceeef 0%, #3a3d40 12%, #1c1e20 52%, #1580d8 78%, rgba(40,170,235,0.9) 100%);
  }
  .grass-symbol {
    position: absolute; left: 240px; top: 310px; width: 125px; height: 150px; border-radius: 50%;
    background: radial-gradient(circle, #4fa83a 0%, #3d8f2d 45%, rgba(61,143,45,0) 70%);
  }

  .benefits { position: absolute; left: 105px; top: 481px; width: 258px; list-style: none; }
  .benefits li { color: var(--white); font-size: 14px; line-height: 15px; padding: 5px 0 5px; border-bottom: 1px solid var(--rule-light); }
  .benefits li:last-child { border-bottom: none; }

  .trust { position: absolute; left: 419px; top: 656px; width: 160px; color: var(--white); font-size: 10.5px; line-height: 13.5px; }
  .trust strong { display: block; margin-top: 2px; color: var(--orange); font-size: 15px; line-height: 20px; font-weight: 400; }

  .footer-brand { position: absolute; left: 0; top: 735px; width: 237px; height: 87px; background: var(--ink); }
  .footer-brand .brand-name { position: absolute; left: 43px; top: 14px; color: var(--white); font-weight: 700; font-size: 36px; line-height: 38px; letter-spacing: -0.5px; }
  .footer-brand .brand-tag { position: absolute; left: 43px; top: 55px; color: var(--white); font-weight: 700; font-size: 11px; }
  .footer-contact { position: absolute; left: 237px; top: 735px; width: 343px; height: 87px; background: linear-gradient(90deg, var(--orange), var(--orange-deep)); color: var(--white); }
  .contact-title { position: absolute; left: 20px; top: 10px; font-family: "Rubik", sans-serif; font-weight: 600; font-size: 14px; }
  .contact-note { position: absolute; left: 20px; top: 28px; width: 190px; font-size: 8.5px; line-height: 10.5px; text-transform: uppercase; }
  .contact-phone { position: absolute; left: 19px; top: 53px; font-family: "Rubik", sans-serif; font-weight: 600; font-size: 22px; }
  .contact-web { position: absolute; left: 195px; top: 56px; width: 134px; height: 20px; background: var(--ink); font-size: 12px; line-height: 20px; text-align: center; }

  /* ---------- Back: air to air heat pumps ---------- */
  .ac-photo {
    position: absolute; left: 323px; top: 60px; width: 257px; height: 707px;
    background: linear-gradient(180deg, #d9dadb 0%, #26282a 22%, #1b1d1f 38%, #eeeeec 48%, #f3ece4 70%, #f6f3ef 100%);
  }
  .leaf-strip { position: absolute; left: 0; top: 247px; width: 26px; height: 520px; background: linear-gradient(180deg, #2d7a2a, #7fc04a 40%, #e9f2e0 80%, #ffffff); }
  .ac-headline { position: absolute; left: 51px; top: 62px; font-family: "Rubik", sans-serif; }
  .ac-headline .title { display: block; color: var(--sky); font-weight: 700; font-size: 38px; line-height: 44px; letter-spacing: -0.5px; }
  .ac-headline .subtitle { display: block; color: var(--white); font-weight: 700; font-size: 30px; line-height: 40px; }
  .ac-headline .tagline { display: block; color: var(--white); font-weight: 400; font-size: 27px; line-height: 38px; }
  .ac-headline .tagline .warm { color: var(--orange); }
  .blue-rule { position: absolute; left: 58px; top: 261px; width: 90px; height: 4px; background: var(--sky); }
  .ac-intro { position: absolute; left: 58px; top: 277px; width: 240px; font-size: 14px; line-height: 18.3px; }

  .features { position: absolute; left: 99px; top: 444px; width: 165px; list-style: none; }
  .features li { font-size: 15px; line-height: 20px; padding: 5px 0 5px; border-bottom: 1px solid var(--rule-dark); }
  .features li:last-child { border-bottom: none; }

  .ac-brand { position: absolute; left: 61px; top: 675px; }
  .ac-brand .brand-name { display: block; font-weight: 700; font-size: 40px; line-height: 44px; letter-spacing: -0.5px; color: var(--ink); }
  .ac-brand .brand-tag { display: block; font-weight: 700; font-size: 13px; color: var(--ink); }
  .office { position: absolute; left: 372px; top: 691px; font-size: 10.3px; line-height: 13px; }
  .contact-row { position: absolute; left: 62px; top: 738px; width: 515px; height: 24px; font-size: 12px; }
  .contact-row .item { position: absolute; top: 6px; display: flex; align-items: center; gap: 5px; }
  .contact-row .phone { top: 0; font-weight: 700; font-size: 21px; gap: 4px; }
  .offer-bar {
    position: absolute; left: 0; top: 767px; width: 580px; height: 55px;
    background: linear-gradient(90deg, var(--orange-deep), var(--orange));
    color: var(--white); font-family: "Roboto Condensed", "Arial Narrow", sans-serif; font-weight: 700;
    font-size: 16px; line-height: 55px; text-align: center;
  }
</style>
</head>
<body>
<main class="canvas">

  <!-- Front side -->
  <div class="sheet sheet--front">
    <article class="flyer flyer--air-source">
      <div class="hero-band"></div>
      <div class="family-photo" role="img" aria-label="Photo of a smiling family sitting together at home, parents forming a roof shape with their arms"></div>

      <h1 class="headline">
        <span>Save Energy and</span>
        <span class="light">Reduce Your</span>
        <span>Carbon Footprint with</span>
        <span class="accent">Heat Pumps!</span>
      </h1>
      <p class="subhead">Discover the Benefits of Air Source and<br>Air to Air Heat Pumps for Your Home</p>

      <svg class="layer" width="580" height="822" viewBox="0 0 580 822" aria-hidden="true">
        <defs>
          <linearGradient id="benefitBlue" x1="0" y1="0" x2="1" y2="0.3">
            <stop offset="0" stop-color="#0b56b3"/>
            <stop offset="0.55" stop-color="#1b8fe0"/>
            <stop offset="1" stop-color="#3cc6f4"/>
          </linearGradient>
        </defs>
        <rect x="0" y="463" width="580" height="272" fill="url(#benefitBlue)"/>
      </svg>

      <div class="pump-photo" role="img" aria-label="Photo of an outdoor air source heat pump unit beside a house"></div>
      <div class="grass-symbol" role="img" aria-label="Green grass power symbol illustration"></div>

      <svg class="layer" width="580" height="822" viewBox="0 0 580 822" aria-hidden="true">
        <polygon points="410,636 580,636 580,735 370,735" fill="#221f20"/>
      </svg>

      <section class="intro">
        <h2>JOIN THE HEAT PUMP<br>REVOLUTION</h2>
        <p>Air Source Heat Pumps (ASHP) are the<br>new green alternative to your oil or gas<br>boiler for your homes heating and hot<br>water requirements that will help build<br>towards a cleaner environment for<br>future generations.</p>
      </section>

      <svg class="layer" width="580" height="822" viewBox="0 0 580 822" fill="none" stroke="#cfe6fb" stroke-width="2.2" aria-hidden="true">
        <circle cx="70" cy="494" r="15"/>
        <text x="70" y="501" text-anchor="middle" font-size="19" fill="#cfe6fb" stroke="none" font-family="Arimo, sans-serif">$</text>
        <path d="M62 548 l11 -11 l5 5 l-11 11 z M62 560 h11 M62 565 h11"/>
        <circle cx="63" cy="612" r="6"/><circle cx="76" cy="604" r="5.5"/><circle cx="73" cy="620" r="5"/>
        <path d="M58 680 l16 -20 l5 5 l-20 15 z M58 680 l-4 5"/>
        <text x="66" y="715" text-anchor="middle" font-size="24" fill="#cfe6fb" stroke="none" font-family="Arimo, sans-serif">$</text>
        <path d="M52 720 q16 8 32 -6"/>
      </svg>

      <ul class="benefits">
        <li>Reduce your energy bills</li>
        <li>Safeguard against rising fuel prices.</li>
        <li>No chimneys or flues producing<br>harmful emissions</li>
        <li>Raise your property value</li>
        <li>Reduce your home's carbon footprint</li>
        <li>Power your home with 100%<br>renewable energy</li>
        <li>Receive as much as £13,900 in<br>payment from the Renewable Heat<br>Incentive</li>
      </ul>

      <p class="trust">Trust Harlow- Climawell Services for Your Heat Pump <strong>Installation and<br>Maintenance</strong></p>

      <footer>
        <div class="footer-brand">
          <span class="brand-name">Harlow</span>
          <span class="brand-tag">Climawell Services</span>
        </div>
        <div class="footer-contact">
          <span class="contact-title">CONTACT US TODAY</span>
          <span class="contact-note">To learn more about how heat pumps can benefit your home!</span>
          <span class="contact-phone">0800 555 0192</span>
          <span class="contact-web">www.harlowcs.co.uk</span>
        </div>
      </footer>
    </article>
  </div>

  <!-- Back side -->
  <div class="sheet sheet--back">
    <article class="flyer flyer--air-to-air">
      <div class="ac-photo" role="img" aria-label="Photo of a wall-mounted air conditioning unit above a mother lifting her young daughter"></div>
      <svg class="layer" width="580" height="822" viewBox="0 0 580 822" aria-hidden="true">
        <polygon points="0,0 580,0 580,75 323,247 0,247" fill="#221f20"/>
      </svg>
      <div class="leaf-strip" role="img" aria-label="Soft green leaf photo at the edge"></div>

      <h1 class="ac-headline">
        <span class="title">AIR CONDITIONING</span>
        <span class="subtitle">FOR THE HOME</span>
        <span class="tagline">Cools in Summer,</span>
        <span class="tagline"><span class="warm">Heats</span> in <span class="warm">Winter</span></span>
      </h1>

      <div class="blue-rule"></div>
      <p class="ac-intro">Enhance the comfort of your<br>home with an Air Conditioning<br>heat pump. We supply and fit<br>latest energy-efficient systems to<br>keep your living space at the right<br>temperature all year round and<br>help reduce your heating bills.</p>

      <svg class="layer" width="580" height="822" viewBox="0 0 580 822" fill="none" stroke="#9a9a9a" stroke-width="1.6" aria-hidden="true">
        <circle cx="66" cy="458" r="9"/><path d="M62 468 v6 h8 v-6 M54 448 l-4 -4 M78 448 l4 -4 M66 444 v-5"/>
        <circle cx="66" cy="500" r="8"/><path d="M66 508 v16 M58 524 h16 M66 516 q-8 -2 -10 -8"/>
        <circle cx="68" cy="570" r="14"/>
        <text x="68" y="577" text-anchor="middle" font-size="18" fill="#9a9a9a" stroke="none" font-family="Arimo, sans-serif">$</text>
        <path d="M58 628 h20 l6 8 l-16 18 l-16 -18 z M52 636 h32"/>
      </svg>

      <ul class="features">
        <li>Cools in summer</li>
        <li>Efficiently heats in<br>winter</li>
        <li>Reduce heating bills</li>
        <li>Purifies the air</li>
        <li>Dehumidifier</li>
        <li>Energy efficient<br>systems</li>
      </ul>

      <div class="ac-brand">
        <span class="brand-name">Harlow</span>
        <span class="brand-tag">Climawell Services</span>
      </div>

      <p class="office">Ayr Office<br>Unit 4 Riverside Business Park<br>Harbour Road, Ayr KA0 1AB</p>

      <div class="contact-row">
        <span class="item" style="left:2px">
          <svg width="12" height="9" viewBox="0 0 12 9" fill="none" stroke="#221f20" stroke-width="1.2" aria-hidden="true"><rect x="0.6" y="0.6" width="10.8" height="7.8"/><path d="M0.6 0.6 l5.4 4.4 l5.4 -4.4"/></svg>
          info@harlowcs.co.uk
        </span>
        <span class="item" style="left:145px">
          <svg width="12" height="12" viewBox="0 0 12 12" fill="none" stroke="#221f20" stroke-width="1.1" aria-hidden="true"><circle cx="6" cy="6" r="5.2"/><ellipse cx="6" cy="6" rx="2.3" ry="5.2"/><path d="M0.8 6 h10.4"/></svg>
          www.harlowcs.co.uk
        </span>
        <span class="item phone" style="left:292px">
          <svg width="17" height="17" viewBox="0 0 24 24" fill="#221f20" aria-hidden="true"><path d="M6.6 10.8a15.1 15.1 0 0 0 6.6 6.6l2.2-2.2c.3-.3.7-.4 1-.2 1.1.4 2.3.6 3.6.6.6 0 1 .4 1 1V20c0 .6-.4 1-1 1A17 17 0 0 1 3 4c0-.6.4-1 1-1h3.5c.6 0 1 .4 1 1 0 1.3.2 2.5.6 3.6.1.3 0 .7-.2 1z"/></svg>
          0800 555 0192
        </span>
      </div>

      <div class="offer-bar">Energy-efficient air conditioning systems from only £1,550</div>
    </article>
  </div>

</main>
</body>
</html>
```